Spring Detox sale graphics for social media

You MUST read the Brief in the WORD document and follow the instructions there. I want to create 10 social media graphics (new Instagram size 4:5 (1080 x 1350 pixels) focusing on our Mother’s Day Spring Detox Sale graphics, using any of the pics attached. Use the attached pics, NO RANDOM STOCK PHOTOGRAPHY. For the color scheme of the graphics, they should all be complementary to the product colors or feel like Spring time.

Target Market(s)

primarily women

Requirements
Must have
• the photos and text attached

```html
<!DOCTYPE html>
<html lang="en">
<head>
<meta charset="utf-8">
<title>Mother's Day Spring Detox Sale – Social Set</title>
<link href="https://fonts.googleapis.com/css2?family=League+Gothic&family=Montserrat:wght@700&family=Poppins:wght@600&display=swap" rel="stylesheet">
<style>
  :root{
    --bg:#000;
    --green:#2a6b32;
    --green-deep:#2b6430;
    --pink:#df4f98;
    --maroon:#4b3a41;
    --red:#d3213a;
    --mint:#edfbf0;
    --mint-frame:#d4fcd8;
    --cream:#fdf3ee;
    --blush:#f9ebee;
    --white:#fff;
  }
  *{margin:0;padding:0;box-sizing:border-box}
  html,body{width:1200px;height:2652px;overflow:hidden;background:var(--bg)}
  .sheet{position:relative;width:1200px;height:2652px}
  .post{position:absolute;width:345px;height:430px;overflow:hidden}
  .col-l{left:248px}.col-r{left:606px}
  .row-1{top:215px}.row-2{top:663px}.row-3{top:1109px}.row-4{top:1557px}.row-5{top:2003px}
  .t{position:absolute;font-family:"League Gothic",sans-serif;line-height:.78;white-space:nowrap;text-transform:uppercase}
  .t.mixed{text-transform:none}
  .center{left:0;width:100%;text-align:center}
  .green{color:var(--green)}.pink{color:var(--pink)}.maroon{color:var(--maroon)}.red{color:var(--red)}
  .pct{position:absolute;display:flex;align-items:flex-start;font-family:"League Gothic",sans-serif;line-height:.78;text-transform:uppercase;white-space:nowrap}
  .pct.center{justify-content:center}
  .pct .num{font-size:1em}
  .pct .side{display:flex;flex-direction:column;margin-left:.06em;margin-top:.02em}
  .pct .sign{font-size:.5em}
  .pct .off{font-size:.36em;margin-top:.12em}
  .note{position:absolute;font-family:"Montserrat",sans-serif;font-weight:700;font-size:15px;color:#222;white-space:nowrap}
  .sub{position:absolute;font-family:"Poppins",sans-serif;font-weight:600;font-size:26px;color:var(--green);white-space:nowrap}
  .ph{position:absolute}
  .bottles{background:linear-gradient(90deg,#f2f2f2,#e9e4ee 30%,#f3f3f3 50%,#e6efec 70%,#eceef6);border-radius:10px}
  .post-1{background:var(--cream)}
  .post-2,.post-3{background:var(--mint)}
  .post-4{background:var(--cream)}
  .post-5{background:linear-gradient(160deg,#e6e6e8,#cfcfd3)}
  .post-6{background:var(--white)}
  .post-7{background:var(--mint-frame)}
  .post-8{background:var(--cream)}
  .post-9,.post-10{background:var(--blush)}
  .inner-frame{position:absolute;left:23px;top:21px;width:296px;height:383px;background:var(--white)}
  .badge{position:absolute;left:228px;top:122px;width:100px;height:100px;border-radius:50%;background:var(--green);color:var(--white)}
</style>
</head>
<body>
<main class="sheet">

  <section class="post post-1 col-l row-1">
    <div class="ph" role="img" aria-label="Watercolour spring flowers and leaves framing the post" style="inset:0;background:radial-gradient(circle at 50% 50%,#fdf1ec 55%,#f7d9d3 80%,#e7eccd 100%)"></div>
    <div class="t green" style="left:50px;top:45px;font-size:49px">Mother’s Day</div>
    <div class="t pink" style="left:48px;top:92px;font-size:100px">Spring</div>
    <div class="t green" style="left:50px;top:174px;font-size:70px">Detox Sale</div>
    <div class="pct green" style="left:50px;top:234px;font-size:93px"><span class="num">25</span><span class="side"><span class="sign">%</span><span class="off">Off</span></span></div>
    <div class="note" style="left:182px;top:258px">Everything!</div>
    <div class="ph" role="img" aria-label="Line illustration of a mother holding her child" style="left:198px;top:280px;width:105px;height:148px;background:linear-gradient(160deg,#f1c6bd,#e8887c);border-radius:50px 50px 10px 10px"></div>
  </section>

  <section class="post post-2 col-r row-1">
    <svg class="ph" width="345" height="430" viewBox="0 0 345 430" aria-hidden="true">
      <circle cx="114" cy="-40" r="170" fill="var(--green-deep)"/>
    </svg>
    <div class="ph" role="img" aria-label="Photo of a smiling woman in a kitchen with the supplement bottles" style="left:150px;top:-18px;width:240px;height:240px;border-radius:50%;background:linear-gradient(170deg,#7a5442,#d8d3cf 60%,#f2f2f2)"></div>
    <div class="pct green" style="left:20px;top:138px;font-size:97px"><span class="num">25</span><span class="side"><span class="sign">%</span><span class="off">Off</span></span></div>
    <div class="t green" style="left:20px;top:225px;font-size:49px">Mother’s Day</div>
    <div class="t pink" style="left:19px;top:275px;font-size:97px">Spring</div>
    <div class="t green" style="left:20px;top:359px;font-size:65px">Detox Sale</div>
  </section>

  <section class="post post-3 col-l row-2">
    <div class="pct green center" style="top:20px;font-size:118px"><span class="num">25</span><span class="side"><span class="sign">%</span><span class="off">Off</span></span></div>
    <div class="sub center" style="top:116px;text-align:center">All Supplements</div>
    <div class="t pink center" style="top:153px;font-size:97px">Spring</div>
    <div class="t green center" style="top:231px;font-size:63px">Detox Sale</div>
    <div class="ph bottles" role="img" aria-label="Four supplement bottles: Nuvella Liver, Nuvella Gut, Nuvella Balance, Nuvella Glucose" style="left:42px;top:295px;width:260px;height:130px"></div>
  </section>

  <section class="post post-4 col-r row-2">
    <div class="ph" role="img" aria-label="Photo of a smiling woman in a white knit top standing behind the supplement bottles" style="left:0;top:0;width:176px;height:430px;background:linear-gradient(180deg,#f6efe9,#e9e2dd 50%,#ece8ea)"></div>
    <div class="pct green" style="left:190px;top:20px;font-size:97px"><span class="num">25</span><span class="side"><span class="sign">%</span><span class="off">Off</span></span></div>
    <div class="t pink" style="left:186px;top:102px;font-size:62px">Spring</div>
    <div class="t pink" style="left:186px;top:151px;font-size:62px">Detox</div>
    <div class="t pink" style="left:186px;top:200px;font-size:62px">Sale</div>
    <div class="t mixed green" style="left:220px;top:258px;font-size:44px">Spring</div>
    <div class="t mixed green" style="left:220px;top:296px;font-size:44px">Reset</div>
    <div class="t mixed green" style="left:220px;top:334px;font-size:44px">Summer</div>
    <div class="t mixed green" style="left:220px;top:369px;font-size:44px">Ready</div>
  </section>

  <section class="post post-5 col-l row-3">
    <div class="ph" role="img" aria-label="Pink cherry blossom branch" style="left:150px;top:0;width:195px;height:120px;background:linear-gradient(200deg,#f3a7b4,#f7d3da 60%,transparent)"></div>
    <div class="pct maroon" style="left:45px;top:49px;font-size:97px"><span class="num">25</span><span class="side"><span class="sign">%</span><span class="off">Off</span></span></div>
    <div class="note" style="left:190px;top:82px">Everything!</div>
    <div class="t maroon" style="left:48px;top:133px;font-size:53px">Mother’s Day</div>
    <div class="t red" style="left:47px;top:180px;font-size:104px">Spring</div>
    <div class="t red" style="left:48px;top:262px;font-size:70px">Detox Sale</div>
    <div class="ph bottles" role="img" aria-label="Four supplement bottles from the detox line" style="left:110px;top:325px;width:182px;height:105px"></div>
  </section>

  <section class="post post-6 col-r row-3">
    <div class="pct pink center" style="top:26px;font-size:104px"><span class="num">25</span><span class="side"><span class="sign">%</span><span class="off">Off</span></span></div>
    <div class="t green center" style="top:119px;font-size:56px">Mother’s Day</div>
    <div class="t green center" style="top:168px;font-size:142px">Sale</div>
    <div class="t mixed pink center" style="top:285px;font-size:72px">Feel Amazing</div>
    <div class="t mixed pink center" style="top:344px;font-size:72px">Again!</div>
  </section>

  <section class="post post-7 col-l row-4">
    <div class="inner-frame"></div>
    <div class="pct pink center" style="top:39px;font-size:100px"><span class="num">25</span><span class="side"><span class="sign">%</span><span class="off">Off</span></span></div>
    <div class="t green center" style="top:134px;font-size:85px">Mother’s</div>
    <div class="t green center" style="top:200px;font-size:85px">Day Sale</div>
    <div class="t pink center" style="top:272px;font-size:72px">Refresh</div>
    <div class="t pink center" style="top:330px;font-size:76px">Your Body</div>
  </section>

  <section class="post post-8 col-r row-4">
    <div class="t pink" style="left:18px;top:38px;font-size:77px">Spring Detox</div>
    <div class="t pink" style="left:18px;top:103px;font-size:108px">Sale</div>
    <div class="badge"><div class="pct" style="left:14px;top:30px;font-size:56px"><span class="num">25</span><span class="side"><span class="sign">%</span><span class="off">Off</span></span></div></div>
    <div class="t mixed green" style="left:18px;top:201px;font-size:50px">Spring Cleanse</div>
    <div class="t mixed green" style="left:18px;top:248px;font-size:50px">Summer Glow</div>
    <div class="ph bottles" role="img" aria-label="Four supplement bottles: Nuvella Liver, Nuvella Gut, Nuvella Balance, Nuvella Glucose" style="left:22px;top:295px;width:300px;height:130px"></div>
  </section>

  <section class="post post-9 col-l row-5">
    <div class="ph" role="img" aria-label="Pink silhouette illustration of a mother holding her baby" style="left:205px;top:8px;width:135px;height:190px;background:linear-gradient(170deg,#f25a6e,#f7a6b0 75%,transparent);border-radius:60px 60px 20px 20px"></div>
    <div class="pct green" style="left:30px;top:68px;font-size:97px"><span class="num">25</span><span class="side"><span class="sign">%</span><span class="off">Off</span></span></div>
    <div class="t green" style="left:30px;top:159px;font-size:53px">Mother’s Day</div>
    <div class="t green" style="left:29px;top:208px;font-size:104px">Sale</div>
    <div class="t pink" style="left:30px;top:309px;font-size:46px">Detox this spring.</div>
    <div class="t pink" style="left:30px;top:348px;font-size:46px">Shine this summer</div>
  </section>

  <section class="post post-10 col-r row-5">
    <div class="ph bottles" role="img" aria-label="Four supplement bottles from the detox line" style="left:170px;top:22px;width:170px;height:95px"></div>
    <div class="pct green" style="left:35px;top:63px;font-size:97px"><span class="num">25</span><span class="side"><span class="sign">%</span><span class="off">Off</span></span></div>
    <div class="t green" style="left:35px;top:148px;font-size:62px">Mother’s Day</div>
    <div class="t green" style="left:34px;top:202px;font-size:104px">Sale</div>
    <div class="t pink" style="left:35px;top:291px;font-size:70px">Spring Detox</div>
    <div class="t pink" style="left:35px;top:346px;font-size:48px">For a summer body</div>
  </section>

</main>
</body>
</html>
```